Harborline Auto LLC

Car Dealer Customer Service
Address: 2874 Cresthaven Road, Shelbyville, TN 37162
web: www.harborlineautoxq.net
email: harborlineautoxq@mailnest.example
Phone: (931) 555-0148
Phone: (629) 555-0173

```html
<!DOCTYPE html>
<html lang="en">
<head>
<meta charset="utf-8">
<title>Harborline Auto LLC – Business Card</title>
<link rel="stylesheet" href="https://fonts.googleapis.com/css2?family=Poppins:wght@400;600;700&display=swap">
<style>
  :root {
    --backdrop: #e9e4dc;
    --card: #f7f7f5;
    --navy-teal: #1d5f80;
    --band-blue: #1f6a8c;
    --band-blue-dark: #17556f;
    --gold: #e3a82b;
    --ink: #2b2b2b;
    --band-text: #e9eef1;
  }
  * { margin: 0; padding: 0; box-sizing: border-box; }
  html, body {
    width: 1200px; height: 1054px; overflow: hidden;
    background: var(--backdrop);
    font-family: "Poppins", sans-serif;
  }
  .card {
    position: absolute; left: 80px; top: 230px;
    width: 1040px; height: 594px;
    background: var(--card);
    border-radius: 26px;
    overflow: hidden;
    box-shadow: 0 10px 40px rgba(0,0,0,0.12);
  }
  .brand {
    position: absolute; left: 30px; top: 150px; width: 430px;
    display: flex; flex-direction: column; align-items: center;
  }
  .brand-dot {
    width: 150px; height: 150px; border-radius: 50%;
    background: var(--navy-teal);
  }
  .brand-name {
    margin-top: 34px;
    font-weight: 700; font-size: 38px; letter-spacing: 0.5px;
    color: var(--navy-teal); white-space: nowrap;
  }
  .details {
    position: absolute; left: 516px; top: 100px; width: 496px; color: var(--ink);
  }
  .person-name {
    font-weight: 700; font-size: 37px; line-height: 1.2; color: var(--navy-teal);
    white-space: nowrap;
  }
  .person-role { font-size: 24px; line-height: 1.4; }
  .address { margin-top: 36px; font-size: 24px; line-height: 1.45; }
  .contacts { margin-top: 24px; list-style: none; }
  .contacts li {
    display: flex; align-items: center; gap: 14px;
    font-size: 23px; line-height: 36px; white-space: nowrap;
  }
  .contacts .phone { font-weight: 600; color: var(--navy-teal); letter-spacing: 0.5px; }
  .contacts svg { width: 19px; height: 19px; flex: none; }
  .band-gold {
    position: absolute; left: 0; bottom: 0; width: 480px; height: 20px;
    background: var(--gold);
  }
  .band-blue {
    position: absolute; right: 0; bottom: 0; width: 600px; height: 74px;
    background: linear-gradient(90deg, var(--band-blue-dark), var(--band-blue));
    clip-path: polygon(36px 0, 100% 0, 100% 100%, 0 100%);
    display: flex; align-items: center; padding-left: 96px;
  }
  .band-blue span {
    font-weight: 700; font-size: 24px; color: var(--band-text); letter-spacing: 0.5px;
  }
</style>
</head>
<body>
  <div class="card">
    <div class="brand">
      <div class="brand-dot"></div>
      <div class="brand-name">HARBORLINE AUTO</div>
    </div>

    <div class="details">
      <div class="person-name">Daniel Warrick</div>
      <div class="person-role">Managing Director</div>
      <div class="address">2874 Cresthaven Road,<br>Shelbyville, TN 37162</div>
      <ul class="contacts">
        <li class="phone">
          <svg viewBox="0 0 20 20" aria-hidden="true"><path fill="#e3a82b" d="M2 8c0-3 3-5 8-5s8 2 8 5v1h-4V7H6v2H2zM5 10h10l2 7H3zm5 1.5a2 2 0 1 0 0 4 2 2 0 0 0 0-4z"/></svg>
          931-555-0148
        </li>
        <li class="phone">
          <svg viewBox="0 0 20 20" aria-hidden="true"><path fill="#e3a82b" d="M2 8c0-3 3-5 8-5s8 2 8 5v1h-4V7H6v2H2zM5 10h10l2 7H3zm5 1.5a2 2 0 1 0 0 4 2 2 0 0 0 0-4z"/></svg>
          629-555-0173
        </li>
        <li>
          <svg viewBox="0 0 20 20" aria-hidden="true"><rect x="1" y="4" width="18" height="12" rx="1" fill="#e3a82b"/><path d="M2 5l8 6 8-6" fill="none" stroke="#f7f7f5" stroke-width="1.5"/></svg>
          www.harborlineautoxq.net
        </li>
        <li>
          <svg viewBox="0 0 20 20" aria-hidden="true"><circle cx="10" cy="10" r="8.5" fill="#e3a82b"/><path d="M1.5 10h17M10 1.5c-4 4-4 13 0 17M10 1.5c4 4 4 13 0 17" fill="none" stroke="#f7f7f5" stroke-width="1.2"/></svg>
          harborlineautoxq@mailnest.example
        </li>
      </ul>
    </div>

    <div class="band-gold"></div>
    <div class="band-blue"><span>HARBORLINE AUTO LLC</span></div>
  </div>
</body>
</html>
```